This book will apply the 12 Steps to gaming addiction, also known as video game addiction. The primary purpose of the book is to provide an effective solution for this new type of addiction. The solution is based on the rich and successful concepts of traditional twelve-step programs like RQ.

The title on the cover will be "Nine Doors Out of the Endless Level" and "by Peter Halvorn". A subtitle can be used if it works in your design of "A Practical Path Back from Compulsive Screen Play". Cover will be for a 6" x 9" book approximately 110 pages in length.

Some back cover text including some review quotes and an author bio are in the attached Word doc. There is also an author photo attached for for the back cover.

Requirements
Must have
• For the cover design it could be stylized, or an image, a partial image, or whatever. I am open to suggestions. Think about what would be noticed by a person searching for help with moderating their video game use, or by the parents or loved ones of problem gamers. Something contemporary and eye catching.

```html
<!DOCTYPE html>
<html lang="en">
<head>
<meta charset="utf-8">
<title>Nine Doors Out of the Endless Level — Book Cover</title>
<link href="https://fonts.googleapis.com/css2?family=Orbitron:wght@600;800;900&family=Poppins:wght@300;400;600;700&display=swap" rel="stylesheet">
<style>
  :root {
    --page: #dcdcdc;
    --ink: #0d0d10;
    --ink-soft: #17171c;
    --white: #f4f4f6;
    --grey-text: #b9b9c2;
    --neon-pink: #ff2fb4;
    --neon-magenta: #d91e8f;
    --neon-blue: #3fa9ff;
    --neon-cyan: #5fe0ff;
    --violet: #4a2bd6;
  }
  * { margin: 0; padding: 0; box-sizing: border-box; }
  html, body { width: 1200px; height: 1200px; overflow: hidden; }
  body {
    background: var(--page);
    position: relative;
    font-family: "Poppins", sans-serif;
  }
  .cover {
    position: absolute;
    top: 210px;
    width: 520px;
    height: 780px;
    overflow: hidden;
    background: var(--ink);
    box-shadow: 0 18px 40px rgba(0,0,0,0.25);
  }

  /* ---------- Back cover ---------- */
  .back-cover { left: 60px; background: linear-gradient(180deg, var(--ink-soft), var(--ink)); }
  .back-glow {
    position: absolute; left: 90px; bottom: 40px; width: 420px; height: 260px;
    background: radial-gradient(ellipse at 55% 60%, rgba(255,47,180,0.75) 0%, rgba(140,40,220,0.45) 35%, rgba(40,30,160,0.2) 60%, transparent 75%);
  }
  .back-content { position: absolute; inset: 44px 40px 40px 40px; color: var(--grey-text); font-size: 9.2px; line-height: 1.55; font-weight: 300; }
  .praise-heading { color: var(--white); font-weight: 700; font-size: 13px; margin-bottom: 12px; }
  .review { text-align: justify; margin-bottom: 10px; }
  .review-source { display: block; text-align: right; font-style: italic; font-size: 7.6px; margin-top: 2px; }
  .divider { height: 2px; margin: 14px 0; background: linear-gradient(90deg, var(--violet), var(--neon-pink)); }
  .blurb p { text-align: justify; margin-bottom: 9px; }
  .author-block { position: absolute; left: 40px; right: 40px; bottom: 40px; display: flex; gap: 22px; align-items: flex-end; }
  .author-photo {
    flex: 0 0 120px; height: 120px; border-radius: 50%;
    background: radial-gradient(circle at 50% 40%, #c9a887 0%, #6d7a4a 45%, #2f3a22 100%);
  }
  .author-bio { color: var(--grey-text); font-size: 9px; line-height: 1.5; font-weight: 300; text-align: justify; }
  .author-bio h3 { color: var(--white); font-size: 11.5px; font-weight: 600; margin-bottom: 6px; }
  .line-pattern { position: absolute; left: 0; bottom: 0; width: 150px; height: 200px;
    background: linear-gradient(45deg, rgba(60,200,120,0.25), rgba(217,30,143,0.2) 60%, transparent); }

  /* ---------- Front cover ---------- */
  .front-cover { left: 620px; background: linear-gradient(160deg, #1a1a20 0%, var(--ink) 55%, #08080a 100%); }
  .neon-numeral {
    position: absolute; left: 90px; top: 60px; width: 380px; height: 300px;
    background:
      radial-gradient(ellipse at 30% 55%, rgba(255,47,180,0.85) 0%, rgba(255,47,180,0.25) 35%, transparent 60%),
      radial-gradient(ellipse at 70% 45%, rgba(63,169,255,0.85) 0%, rgba(63,169,255,0.25) 35%, transparent 62%);
    filter: blur(2px);
  }
  .light-streaks { position: absolute; inset: 0; }
  .front-title {
    position: absolute; left: 40px; right: 40px; top: 350px;
    font-family: "Orbitron", sans-serif; color: var(--white); text-align: right;
    font-weight: 900; text-transform: uppercase; line-height: 0.98;
  }
  .front-title .t-small { display: block; font-size: 30px; letter-spacing: 1px; }
  .front-title .t-big { display: block; font-size: 60px; letter-spacing: 1px; }
  .front-subtitle {
    position: absolute; left: 40px; right: 40px; top: 598px;
    font-family: "Orbitron", sans-serif; font-weight: 600; color: var(--white);
    font-size: 10.5px; letter-spacing: 2.4px; text-transform: uppercase; text-align: right;
  }
  .front-author {
    position: absolute; left: 40px; right: 40px; top: 640px;
    font-family: "Orbitron", sans-serif; font-weight: 800; color: var(--white);
    font-size: 22px; letter-spacing: 1.5px; text-align: right;
  }
  .corner-lines { position: absolute; right: 60px; bottom: 0; width: 200px; height: 70px;
    background: linear-gradient(20deg, transparent 20%, rgba(217,30,143,0.35) 70%, transparent); }
</style>
</head>
<body>

<section class="cover back-cover" aria-label="Back cover">
  <div class="back-glow"></div>
  <div class="line-pattern" role="img" aria-label="Fine curved line pattern in green and pink"></div>
  <div class="back-content">
    <h2 class="praise-heading">Praise for Nine Doors Out of the Endless Level</h2>
    <p class="review">A must-read for anyone who is addicted to or thinks they may have a problem with digital gaming. This eloquent work will also be useful to academics and clinicians exploring potential solutions. The author recognizes the similarities between gaming addiction and other addictions, and logically applies one of the most effective known solutions for addiction – the Twelve Steps.
      <span class="review-source">– Dale Renshaw, Noted Interventionist and Keynote Speaker</span></p>
    <p class="review">“If you suffer from digital gaming addiction, I strongly encourage you to use this book as your road map to get you back to the real world.”
      <span class="review-source">– Owen Callister, Founder of Feedline Weekly</span></p>
    <p class="review">“As a high school teacher for 24 years, husband, father, coach, and 12-Step member, I can assure you that this book will transform the life of anyone who is addicted to video games. Well written, easy to understand, and a wonderful book that will provide you with a clear road map to recovery, and this includes teenagers, a group I have been working with in the classroom for decades.”
      <span class="review-source">– Tomas Reyna, Harlow Bay, OR High School Teacher</span></p>
    <div class="divider"></div>
    <div class="blurb">
      <p>An effective solution to the challenge of Digital Gaming Addiction (aka Video Game Addiction) based on the rich and successful tradition of the Twelve Steps.</p>
      <p>Addiction to Digital Gaming is a new and troubling phenomenon that has burst upon an unprepared society with alarming speed. Many people crave the use of Digital Games in a strikingly similar way to any other addict. Digital Games are a complex software and hardware system that have been designed to promote continued and progressive usage. This sophisticated technology clearly feeds on natural addictive tendencies.</p>
      <p>The 12 Steps are one of the most effective methods for treating addiction in human history. Originating with Recovery Quorum in 1939, the 12 Steps have since been used to treat a variety of other addictions, including drugs, sex, gambling, eating disorders, and many others. Now in this groundbreaking work the 12 Steps are applied to the complex and evolving contemporary phenomenon of Digital Gaming Addiction.</p>
    </div>
  </div>
  <div class="author-block">
    <div class="author-photo" role="img" aria-label="Author portrait photograph"></div>
    <div class="author-bio">
      <h3>About the Author</h3>
      <p>Peter Halvorn is a Technology Consultant and Writer with many years of professional coding and consulting experience. He also struggled with addiction to drugs and alcohol and is now clean and sober in a Twelve-Step program for over 17 years. This unique combination of 12-Step experience and technology expertise led him to write Nine Doors Out of the Endless Level.</p>
    </div>
  </div>
</section>

<section class="cover front-cover" aria-label="Front cover">
  <div class="neon-numeral" role="img" aria-label="Glowing pink and blue neon title artwork"></div>
  <svg class="light-streaks" viewBox="0 0 520 780" aria-hidden="true">
    <defs>
      <linearGradient id="streakPink" x1="0" x2="1">
        <stop offset="0" stop-color="#ff2fb4" stop-opacity="0"/>
        <stop offset="0.5" stop-color="#ff2fb4"/>
        <stop offset="1" stop-color="#ff2fb4" stop-opacity="0"/>
      </linearGradient>
      <linearGradient id="streakBlue" x1="0" x2="1">
        <stop offset="0" stop-color="#3fa9ff" stop-opacity="0"/>
        <stop offset="0.5" stop-color="#5fe0ff"/>
        <stop offset="1" stop-color="#3fa9ff" stop-opacity="0"/>
      </linearGradient>
    </defs>
    <line x1="10" y1="520" x2="60" y2="380" stroke="url(#streakPink)" stroke-width="4"/>
    <line x1="20" y1="700" x2="90" y2="560" stroke="url(#streakPink)" stroke-width="3"/>
    <line x1="0" y1="330" x2="260" y2="380" stroke="url(#streakBlue)" stroke-width="1.5"/>
    <line x1="330" y1="560" x2="520" y2="590" stroke="url(#streakPink)" stroke-width="2"/>
    <line x1="460" y1="200" x2="430" y2="330" stroke="url(#streakBlue)" stroke-width="2"/>
  </svg>
  <h1 class="front-title">
    <span class="t-small">Nine Doors</span>
    <span class="t-small">Out of the</span>
    <span class="t-big">Endless</span>
    <span class="t-big">Level</span>
  </h1>
  <p class="front-subtitle">A Practical Path Back from Compulsive Screen Play</p>
  <p class="front-author">by Peter Halvorn</p>
  <div class="corner-lines" role="img" aria-label="Fine pink curved line pattern"></div>
</section>

</body>
</html>
```